Business Card Design (NEW FILES)

ATTENTION: New vector files are available. Please update your design to reflect/use the new (better resolution) logo images.

Seeking a unique and professional business card design for a commercial drone photography/videography business. The layout should feature
the logo (attached) and include the following information:
Owen Tarrick
614-502-7738
www.skylarkreelworks.example
NRD Certified Remote Pilot

Owen Tarrick

```html
<!DOCTYPE html>
<html lang="en">
<head>
<meta charset="utf-8">
<title>Skylark Reelworks – Business Card</title>
<link rel="stylesheet" href="https://fonts.googleapis.com/css2?family=Arimo:ital,wght@0,400;0,700;1,400&display=swap">
<style>
  :root {
    --stage: #1b1b1f;
    --paper: #ffffff;
    --navy: #121645;
    --orange: #ec8a4c;
    --ink-light: #ffffff;
  }
  * { box-sizing: border-box; margin: 0; padding: 0; }
  html, body {
    width: 1200px;
    height: 963px;
    overflow: hidden;
    background: var(--stage);
  }
  .stage {
    position: relative;
    width: 1200px;
    height: 963px;
  }
  .card {
    position: absolute;
    left: 210px;
    width: 780px;
    height: 445px;
    border-radius: 28px;
    overflow: hidden;
    font-family: "Arimo", Arial, sans-serif;
    box-shadow: 0 16px 40px rgba(0,0,0,0.5);
  }
  .card-front { top: 21px; background: var(--paper); }
  .card-back  { top: 496px; background: var(--navy); }

  .card-waves {
    position: absolute;
    inset: 0;
    width: 100%;
    height: 100%;
  }
  .holder {
    position: absolute;
    left: 48px;
    top: 36px;
  }
  .holder-name {
    font-weight: 700;
    font-size: 24px;
    letter-spacing: 1px;
    text-transform: uppercase;
    color: var(--navy);
  }
  .holder-name .surname { color: var(--orange); }
  .holder-role {
    font-size: 16px;
    color: var(--navy);
    margin-top: 2px;
  }
  .details {
    position: absolute;
    left: 45px;
    top: 228px;
    color: var(--ink-light);
    font-size: 18px;
    line-height: 1.45;
  }
  .details .contact {
    display: flex;
    align-items: center;
    gap: 10px;
  }
  .details .contact-first { margin-top: 10px; }
  .details svg { width: 16px; height: 16px; flex: none; }

  .brand {
    position: absolute;
    display: flex;
    align-items: center;
    gap: 14px;
  }
  .brand-front { left: 437px; top: 156px; }
  .brand-back {
    left: 0;
    right: 0;
    top: 0;
    bottom: 0;
    justify-content: center;
    gap: 20px;
  }
  .brand-mark {
    width: 22px;
    height: 22px;
    border-radius: 50%;
    background: var(--orange);
    flex: none;
  }
  .brand-back .brand-mark { width: 30px; height: 30px; }
  .brand-name {
    font-size: 32px;
    font-weight: 400;
    color: var(--navy);
    letter-spacing: 1px;
    text-transform: uppercase;
    line-height: 1.1;
  }
  .brand-back .brand-name {
    color: var(--ink-light);
    font-size: 46px;
  }
</style>
</head>
<body>
<main class="stage">
  <article class="card card-front">
    <svg class="card-waves" viewBox="0 0 1000 571" preserveAspectRatio="none" aria-hidden="true">
      <path d="M0,150 C170,120 290,170 380,300 C470,430 560,560 780,571 L0,571 Z" fill="var(--navy)"/>
      <path d="M0,128 C190,100 320,150 400,270" fill="none" stroke="var(--orange)" stroke-width="9"/>
      <path d="M330,170 C380,210 410,260 450,330 C520,450 600,540 680,565" fill="none" stroke="var(--navy)" stroke-width="4"/>
      <path d="M560,430 C640,500 720,540 850,545" fill="none" stroke="var(--orange)" stroke-width="9"/>
    </svg>

    <header class="holder">
      <h1 class="holder-name">Owen <span class="surname">Tarrick</span></h1>
      <p class="holder-role">Owner</p>
    </header>

    <section class="details">
      <p>NRD Certified Remote Pilot</p>
      <p>Fully Insured</p>
      <p class="contact contact-first">
        <svg viewBox="0 0 24 24"><path d="M6.6 10.8a15.1 15.1 0 0 0 6.6 6.6l2.2-2.2c.3-.3.7-.4 1-.2 1.1.4 2.3.6 3.6.6.6 0 1 .4 1 1V20c0 .6-.4 1-1 1A17 17 0 0 1 3 4c0-.6.4-1 1-1h3.5c.6 0 1 .4 1 1 0 1.3.2 2.5.6 3.6.1.3 0 .7-.2 1z" fill="var(--orange)"/></svg>
        <span>614-502-7738</span>
      </p>
      <p class="contact">
        <svg viewBox="0 0 24 24" fill="none" stroke="var(--orange)" stroke-width="1.8"><circle cx="12" cy="12" r="9"/><path d="M3 12h18M12 3c3 3.2 3 14.8 0 18M12 3c-3 3.2-3 14.8 0 18"/></svg>
        <span>www.skylarkreelworks.example</span>
      </p>
    </section>

    <div class="brand brand-front">
      <span class="brand-mark"></span>
      <p class="brand-name">Skylark<br>Reelworks</p>
    </div>
  </article>

  <article class="card card-back">
    <div class="brand brand-back">
      <span class="brand-mark"></span>
      <p class="brand-name">Skylark<br>Reelworks</p>
    </div>
  </article>
</main>
</body>
</html>
```